Kestal-Materials. Limestone; improving the world

New Limestone company and need logo design.
Limestone offsets carbon mitigation industries restore and replenish soil fertilities in the Prairies, the breadbasket of the world. At the same time, Limestone is proving a critical emergent component of carbon capture sequestration technology will therefore play a critical role in the development of the western Canadian energy industries
Our limestone resources are situated in the foothills of the Canadian Rockies well-positioned above the sprawling fields of the vast peace district.
Agriculture and oli sites
Kestal Materials
3 page

```html
<!DOCTYPE html>
<html lang="en">
<head>
<meta charset="utf-8">
<title>Kestal Materials</title>
<link href="https://fonts.googleapis.com/css2?family=Teko:wght@500;600&family=Lato:wght@400;700&display=swap" rel="stylesheet">
<style>
:root{
  --navy:#2a3f5c;
  --navy-deep:#223552;
  --pale:#dce6f4;
  --ink:#111418;
  --text:#2b2b2b;
  --white:#ffffff;
  --green:#1d6a14;
  --black:#000000;
}
*{margin:0;padding:0;box-sizing:border-box}
html,body{width:1200px;height:3525px;overflow:hidden}
body{font-family:'Lato',sans-serif;color:var(--text);background:var(--white);position:relative}
.heading{font-family:'Teko',sans-serif;font-weight:600;text-transform:uppercase;letter-spacing:.5px;color:var(--ink);line-height:1}
section,header,footer{position:absolute;left:0;width:1200px}
.abs{position:absolute}
.btn{display:flex;align-items:center;justify-content:center;gap:8px;background:var(--navy);color:var(--white);font-family:'Teko',sans-serif;font-weight:500;font-size:17px;text-transform:uppercase;border-radius:4px;padding-top:3px}
.arrow-dot{width:14px;height:14px;display:inline-block;margin-top:-3px}

/* header */
.site-header{top:0;height:75px;background:var(--navy)}
.brand{left:112px;top:22px;font-family:'Teko',sans-serif;font-weight:600;font-size:30px;color:var(--white);text-transform:uppercase;line-height:1}
.main-nav{left:429px;top:28px;display:flex;gap:21px;font-family:'Teko',sans-serif;font-weight:500;font-size:16px;color:var(--white);text-transform:uppercase;line-height:1}
.phone{left:966px;top:18px;display:flex;align-items:center;gap:12px;color:var(--white);font-family:'Teko',sans-serif;font-weight:500;font-size:16px}
.phone-icon{width:39px;height:39px;border-radius:50%;background:var(--white);display:flex;align-items:center;justify-content:center}

/* hero */
.hero{top:75px;height:557px;background:linear-gradient(180deg,#3d5578 0%,#e89a7a 4%,#34486a 7%,#2f5a2a 18%,#3f6a2c 55%,#6c6a55 80%,#3a4a2a 100%)}
.hero-rock{left:460px;top:150px;width:740px;height:407px;background:radial-gradient(ellipse at 55% 40%,#c9b7ad 0%,#a89089 40%,rgba(90,100,70,0) 72%)}
.hero-badge{left:132px;top:87px;width:388px;height:388px;border-radius:50%;background:rgba(29,106,20,.85);color:var(--white);text-align:center}
.hero-badge h1{font-size:44px;color:var(--white);margin-top:97px}
.hero-badge p{font-size:15px;line-height:30px;margin:12px 18px 0}
.hero-badge .more{display:flex;justify-content:center;align-items:center;gap:6px;margin-top:16px;font-family:'Teko',sans-serif;font-weight:500;font-size:16px;text-transform:uppercase}

/* mission */
.mission{top:632px;height:644px;text-align:center}
.mission h2{font-size:44px;margin-top:80px}
.mission p{font-size:15px;line-height:30px;margin:20px auto 0;width:640px}
.video{left:291px;top:222px;width:626px;height:336px;background:linear-gradient(180deg,#7a7f95 0%,#e0a35a 28%,#f7d28a 34%,#536c9c 55%,#3e5a8a 75%,#6b6a3a 100%);box-shadow:0 6px 18px rgba(0,0,0,.25)}
.play{left:289px;top:144px;width:48px;height:48px;border-radius:50%;background:var(--navy-deep);display:flex;align-items:center;justify-content:center}

/* who we are */
.who{top:1276px;height:611px;background:var(--pale)}
.mosaic{left:118px;top:82px;width:470px;height:448px;display:grid;grid-template-columns:repeat(3,1fr);grid-template-rows:repeat(3,1fr);gap:3px;box-shadow:0 4px 14px rgba(0,0,0,.18)}
.tile{width:100%;height:100%}
.t1{background:linear-gradient(180deg,#a9bccf,#3f7a2e 55%,#5e7a5a)}
.t2{background:linear-gradient(135deg,#8a8a8a,#5d5d5d)}
.t3{background:linear-gradient(135deg,#6a5a4a,#c7b8a2)}
.t4{background:linear-gradient(180deg,#3a66a8,#b38a6a 45%,#8a6a4a)}
.t5{background:linear-gradient(180deg,#c9c3b7,#a39e92)}
.t6{background:linear-gradient(180deg,#4a7ac0,#7a8a6a 50%,#9aa092)}
.t7{background:linear-gradient(135deg,#b0aba5,#e4e0db)}
.t8{background:linear-gradient(180deg,#3b6fb0,#c7a060 60%,#8a8a8a)}
.t9{background:radial-gradient(circle at 50% 70%,#d8561e 0%,#4a2a1e 35%,#1a1a22 80%)}
.who h2{left:651px;top:150px;font-size:36px}
.who p{left:655px;top:204px;width:430px;font-size:15px;line-height:30px}
.who .btn{left:655px;top:407px;width:122px;height:47px}

/* sustainability */
.sustain{top:1887px;height:671px}
.sustain h2{left:112px;top:165px;font-size:36px}
.sustain p{left:112px;top:220px;width:440px;font-size:15px;line-height:30px}
.sustain .btn{left:112px;top:456px;width:122px;height:47px}
.photo-back{left:706px;top:87px;width:382px;height:497px;border-radius:4px;background:linear-gradient(135deg,#c9c4be 0%,#9a8e86 45%,#6e6662 100%)}
.photo-front{left:602px;top:336px;width:382px;height:248px;border-radius:4px;background:linear-gradient(135deg,#3a3a40 0%,#c9531e 40%,#e0a030 60%,#2a2a30 100%);border:1px solid #555}

/* news */
.news{top:2558px;height:610px;background:var(--pale)}
.news-intro{left:138px;top:232px}
.news-intro h2{font-family:'Teko',sans-serif;font-weight:600;font-size:36px;color:var(--ink);line-height:1}
.news-intro p{font-size:15px;line-height:30px;margin-top:10px}
.news-arrows{display:flex;gap:10px;margin-top:10px}
.card{top:58px;width:298px;height:491px;background:var(--white);overflow:hidden}
.card .thumb{height:211px}
.card .body{padding:20px 16px 0}
.card .date{font-size:15px;color:#444}
.card h3{font-family:'Teko',sans-serif;font-weight:600;font-size:26px;line-height:30px;color:var(--ink);margin-top:8px}
.card .excerpt{font-size:15px;line-height:26px;margin-top:10px;width:290px}
.card .more{display:flex;align-items:center;gap:6px;margin-top:12px;font-family:'Teko',sans-serif;font-weight:500;font-size:16px;color:var(--navy);text-transform:uppercase}
.c1{left:349px}.c1 .thumb{background:linear-gradient(135deg,#6a7a4a,#b8a898 50%,#3a3a3a)}
.c2{left:663px}.c2 .thumb{background:linear-gradient(180deg,#2a4a9a 0%,#4a7ad0 45%,#f0a020 75%,#1a2a5a 100%)}
.c3{left:979px}.c3 .thumb{background:linear-gradient(135deg,#c8c6c0,#6a8a3a 50%,#3a4a2a)}

/* footer */
.site-footer{top:3168px;height:357px;background:var(--black);color:var(--white);text-align:center}
.site-footer .brand-foot{font-family:'Teko',sans-serif;font-weight:600;font-size:28px;text-transform:uppercase;margin-top:79px;line-height:1}
.foot-nav{display:flex;justify-content:center;gap:22px;margin-top:24px;font-family:'Teko',sans-serif;font-weight:500;font-size:16px;text-transform:uppercase;line-height:1}
.social{display:flex;justify-content:center;gap:8px;margin-top:30px}
.social span{width:39px;height:39px;border-radius:50%;background:var(--navy)}
.copyright{font-size:15px;margin-top:44px}
</style>
</head>
<body>

<header class="site-header">
  <div class="abs brand">Kestal Materials</div>
  <nav class="abs main-nav"><span>Home</span><span>About Us</span><span>Who We Are</span><span>Mission</span><span>Sustainability</span><span>News</span></nav>
  <div class="abs phone">
    <span class="phone-icon"><svg width="16" height="16" viewBox="0 0 24 24"><path fill="#2a3f5c" d="M6.6 10.8a15.1 15.1 0 0 0 6.6 6.6l2.2-2.2a1 1 0 0 1 1-.25 11.4 11.4 0 0 0 3.6.57 1 1 0 0 1 1 1V20a1 1 0 0 1-1 1A17 17 0 0 1 3 4a1 1 0 0 1 1-1h3.5a1 1 0 0 1 1 1c0 1.25.2 2.45.57 3.57a1 1 0 0 1-.25 1z"/></svg></span>
    <span>100-555-0142</span>
  </div>
</header>

<section class="hero" role="img" aria-label="Forested valley under a sunset sky with a pale limestone outcrop">
  <div class="abs hero-rock"></div>
  <div class="abs hero-badge">
    <h1 class="heading">Kestal Materials</h1>
    <p>Lorem ipsum dolor sit amet, consectetur adip-iscing elit, sed do eiusmod tempor incididunt ut labore et dolore magna aliqua. Quis ipsum suspendisse ultrices gravida.</p>
    <div class="more">Learn More <svg class="arrow-dot" viewBox="0 0 16 16"><circle cx="8" cy="8" r="7" fill="#fff"/><path d="M6 5l3 3-3 3" stroke="#1d6a14" stroke-width="2" fill="none"/></svg></div>
  </div>
</section>

<section class="mission">
  <h2 class="heading">Mission</h2>
  <p>Lorem ipsum dolor sit amet, consectetur adipiscing elit, sed do eiusmod tempor incididunt ut labore et dolore magna aliqua.</p>
  <div class="abs video" role="img" aria-label="Solar panel field at sunrise">
    <div class="abs play"><svg width="14" height="16" viewBox="0 0 14 16"><path d="M2 1l11 7-11 7z" fill="#fff"/></svg></div>
  </div>
</section>

<section class="who">
  <div class="abs mosaic">
    <div class="tile t1" role="img" aria-label="River lined with trees"></div>
    <div class="tile t2" role="img" aria-label="Loader on crushed stone"></div>
    <div class="tile t3" role="img" aria-label="Team giving a high five"></div>
    <div class="tile t4" role="img" aria-label="Excavator in a quarry"></div>
    <div class="tile t5" role="img" aria-label="Pile of white limestone gravel"></div>
    <div class="tile t6" role="img" aria-label="Mountain slope with rocks"></div>
    <div class="tile t7" role="img" aria-label="White mineral pellets"></div>
    <div class="tile t8" role="img" aria-label="Cranes over a construction site"></div>
    <div class="tile t9" role="img" aria-label="Industrial furnace glowing"></div>
  </div>
  <h2 class="abs heading">Who We Are</h2>
  <p class="abs">Lorem ipsum dolor sit amet, consectetur adipiscing elit, sed do eiusmod tempor incididunt ut labore et dolore magna aliqua. Quis ipsum suspendisse ultrices gravida. Risus commodo viverra maecenas accumsan lacus vel facilisis.uis nostrud exercitation ullamco laboris nisi ut aliquip ex ea commodo consequat.</p>
  <div class="abs btn">Learn More <svg class="arrow-dot" viewBox="0 0 16 16"><circle cx="8" cy="8" r="7" fill="#fff"/><path d="M6 5l3 3-3 3" stroke="#2a3f5c" stroke-width="2" fill="none"/></svg></div>
</section>

<section class="sustain">
  <h2 class="abs heading">Sustainability</h2>
  <p class="abs">Lorem ipsum dolor sit amet, consectetur adipiscing elit, sed do eiusmod tempor incididunt ut labore et dolore magna aliqua. Quis ipsum suspendisse ultrices gravida. Risus commodo viverra maecenas accumsan lacus vel facilisis. quis nostrud exercitation ullamco laboris nisi ut aliquip ex ea commodo consequat. Duis aute irure dolor in reprehenderit in voluptate velit esse cillum dolore eu fugiat nulla pariatur.</p>
  <div class="abs btn">Learn More <svg class="arrow-dot" viewBox="0 0 16 16"><circle cx="8" cy="8" r="7" fill="#fff"/><path d="M6 5l3 3-3 3" stroke="#2a3f5c" stroke-width="2" fill="none"/></svg></div>
  <div class="abs photo-back" role="img" aria-label="Colleagues working together in an office"></div>
  <div class="abs photo-front" role="img" aria-label="Workers in hard hats joining hands"></div>
</section>

<section class="news">
  <div class="abs news-intro">
    <h2>Latest News</h2>
    <p>Covering March &amp;<br>April 2021</p>
    <div class="news-arrows">
      <svg width="15" height="15" viewBox="0 0 16 16"><circle cx="8" cy="8" r="7.5" fill="#2a3f5c"/><path d="M10 5l-3 3 3 3" stroke="#fff" stroke-width="2" fill="none"/></svg>
      <svg width="15" height="15" viewBox="0 0 16 16"><circle cx="8" cy="8" r="7.5" fill="#2a3f5c"/><path d="M6 5l3 3-3 3" stroke="#fff" stroke-width="2" fill="none"/></svg>
    </div>
  </div>
  <article class="abs card c1">
    <div class="thumb" role="img" aria-label="Group of friends outdoors"></div>
    <div class="body"><div class="date">April 07 2021</div><h3>Sed ut perspiciatis<br>unde omnis</h3><p class="excerpt">Lorem ipsum dolor sit amet, con-sectetur adipiscing elit, sed do eiusmod tempor incididunt ut labore et dolore magna aliqua.</p><div class="more">Learn More <svg class="arrow-dot" viewBox="0 0 16 16"><circle cx="8" cy="8" r="7" fill="#2a3f5c"/><path d="M6 5l3 3-3 3" stroke="#fff" stroke-width="2" fill="none"/></svg></div></div>
  </article>
  <article class="abs card c2">
    <div class="thumb" role="img" aria-label="Bottling line in a factory"></div>
    <div class="body"><div class="date">April 07 2021</div><h3>Sed ut perspiciatis<br>unde omnis</h3><p class="excerpt">Lorem ipsum dolor sit amet, con-sectetur adipiscing elit, sed do eiusmod tempor incididunt ut labore et dolore magna aliqua.</p><div class="more">Learn More <svg class="arrow-dot" viewBox="0 0 16 16"><circle cx="8" cy="8" r="7" fill="#2a3f5c"/><path d="M6 5l3 3-3 3" stroke="#fff" stroke-width="2" fill="none"/></svg></div></div>
  </article>
  <article class="abs card c3">
    <div class="thumb" role="img" aria-label="Planting and watering a young tree"></div>
    <div class="body"><div class="date">April 07 2021</div><h3>Sed ut perspiciatis<br>unde omnis</h3><p class="excerpt">Lorem ipsum dolor sit amet, con-sectetur adipiscing elit, sed do eiusmod tempor incididunt ut labore et dolore magna aliqua.</p><div class="more">Learn More <svg class="arrow-dot" viewBox="0 0 16 16"><circle cx="8" cy="8" r="7" fill="#2a3f5c"/><path d="M6 5l3 3-3 3" stroke="#fff" stroke-width="2" fill="none"/></svg></div></div>
  </article>
</section>

<footer class="site-footer">
  <div class="brand-foot">Kestal Materials</div>
  <nav class="foot-nav"><span>Home</span><span>About Us</span><span>Who We Are</span><span>Mission</span><span>Sustainability</span><span>News</span></nav>
  <div class="social"><span></span><span></span><span></span><span></span><span></span></div>
  <p class="copyright">©Copyrights 2021 Company Name &nbsp;&nbsp;| &nbsp;&nbsp;All Rights Reserved</p>
</footer>

</body>
</html>
```